Lumbra Ember Oven Kitchen (restaurant)

Restaurant with a cool vibe.
We need a refresh of existing site. Appealing to a hip crowd of 25 or older age bracket (mid price to high small town). Constant changes food and cocktail menu. A vibing atmosphere with jazz funk hip music.
Must be able to scale for any device… phone/mobile device super important.
Instagram: @Lumbra.Bexwell
Website: lumbrabexwell.example

Target Market(s)

25-55 age group

Number of Pages Required

1 page

Font styles to use
Sans Serif

Requirements
Must have
• Simple to navigate. Simplicity is the key to all sophistication.

Links/Buttons
Menu
Gift Cards
Reservations
Take Out
Contact Us
Should not have
• Please, nothing generic looking… no cookie cutter look. Originality

```html
<!DOCTYPE html>
<html lang="en">
<head>
<meta charset="utf-8">
<title>Lumbra Ember Oven Kitchen</title>
<link href="https://fonts.googleapis.com/css2?family=Archivo+Black&family=Poppins:wght@300;400;500;600&family=Roboto:wght@500;700&family=Hind:wght@600&display=swap" rel="stylesheet">
<style>
:root{
  --yellow:#fdd22f;
  --yellow-soft:#fbe27a;
  --ink:#111111;
  --night:#000000;
  --card:#22262b;
  --paper:#ffffff;
  --muted:#555555;
  --food-light:#e9dfd2;
  --brick:#8a5a3c;
}
*{margin:0;padding:0;box-sizing:border-box}
html,body{width:1200px;height:3000px;overflow:hidden;background:var(--paper)}
body{position:relative;font-family:"Poppins",sans-serif;color:var(--ink)}
.abs{position:absolute}
.heading{font-family:"Archivo Black",sans-serif;letter-spacing:.5px}
.btn{position:absolute;display:flex;align-items:center;justify-content:center;border-radius:22px;font-family:"Roboto",sans-serif;font-weight:700;font-size:16px;text-decoration:none;color:var(--ink)}
.btn-solid{background:var(--yellow)}
.btn-line{border:2px solid var(--ink);background:var(--paper)}

/* nav */
.nav{top:0;left:0;width:1200px;height:52px;background:var(--night)}
.nav a{position:absolute;top:20px;color:var(--paper);font-size:13px;text-decoration:none}
.nav a.active{color:var(--yellow)}
.nav a.active::after{content:"";position:absolute;left:50%;top:20px;width:4px;height:4px;margin-left:-2px;border-radius:50%;background:var(--yellow)}
.brand{position:absolute;top:0;left:425px;width:355px;height:124px;z-index:5}
.brand-name{position:absolute;top:16px;left:0;width:355px;text-align:center;font-family:"Archivo Black",sans-serif;color:var(--ink);font-size:31px;line-height:32px}
.brand-name small{display:block;font-size:12px;line-height:14px}

/* hero */
.hero{top:52px;left:0;width:1200px;height:661px;background:radial-gradient(ellipse at 55% 75%,#8c6a40 0%,#a88459 30%,#cdb896 60%,var(--food-light) 85%)}
.hero-title{top:198px;left:0;width:1200px;text-align:center;font-family:"Hind",sans-serif;font-weight:600;font-size:58px;line-height:58px}

/* info band */
.info{top:713px;left:0;width:1200px;height:382px;background:var(--yellow)}
.info .divider{position:absolute;top:0;width:1px;height:382px;background:#e8bd1d}
.info h2{position:absolute;font-size:29px}
.info h3{position:absolute;font-family:"Roboto",sans-serif;font-weight:700;font-size:20px}
.hours{position:absolute;left:85px;font-size:12px;line-height:27px}
.clock{position:absolute;left:60px}
.map{top:818px;left:431px;width:338px;height:187px;background:linear-gradient(135deg,#eceff1,#dfe6e9 60%,#b9d3ea)}
.gift{top:822px;left:802px;width:338px;height:188px;background:linear-gradient(120deg,#f4dada 0%,#fbf1f1 30%,#ffffff 55%)}

/* reservations */
.res-bg{top:1290px;left:0;width:1200px;height:600px;background:linear-gradient(180deg,#ffffff 0%,#efe9df 35%,#e2d8c8 70%,#ffffff 100%)}
.building{top:1340px;left:513px;width:687px;height:580px;background:radial-gradient(ellipse at 60% 45%,#9a6446 0%,var(--brick) 40%,rgba(138,90,60,.55) 70%,rgba(226,216,200,0) 100%)}
.takeout{top:1355px;left:175px;width:338px;height:413px;border-radius:14px;background:var(--card);overflow:hidden}
.takeout-head{height:66px;background:var(--yellow);display:flex;align-items:center;justify-content:center;font-family:"Roboto",sans-serif;font-weight:500;font-size:19px}
.box-food{top:1598px;left:158px;width:335px;height:190px;background:radial-gradient(ellipse at 35% 45%,#c08a52 0%,#a87443 45%,rgba(168,116,67,0) 72%)}

/* order band */
.order-band{top:1845px;left:0;width:1200px;height:380px}
.burger{top:1898px;left:640px;width:390px;height:339px;background:radial-gradient(ellipse at 50% 52%,#7a4433 0%,#a85a4a 30%,rgba(217,178,123,.8) 55%,rgba(253,210,47,0) 72%)}

/* newsletter */
.portrait{top:2264px;left:-88px;width:226px;height:222px;border-radius:50%;background:radial-gradient(circle at 60% 40%,#d9b08a,#a8643a 60%,#5b3a2a)}
.signup{top:2382px;left:344px;width:512px;height:46px;border-radius:23px;border:2px solid var(--yellow-soft);background:var(--paper);overflow:hidden}

/* social strip */
.tile{position:absolute;top:2526px;width:193px;height:188px}

/* footer */
.footer{top:2714px;left:0;width:1200px;height:286px;background:var(--night);color:var(--paper)}
.footer h4{position:absolute;font-family:"Roboto",sans-serif;font-weight:500;font-size:15px}
.footer p{position:absolute;font-size:12px;line-height:20px;text-align:center}
</style>
</head>
<body>

<nav class="abs nav">
  <a class="active" href="#" style="left:140px">Home</a>
  <a href="#" style="left:230px">Menu</a>
  <a href="#" style="left:312px">Reservations</a>
  <a href="#" style="left:815px">Order Online</a>
  <a href="#" style="left:946px">Contact Us</a>
</nav>
<div class="brand">
  <svg width="355" height="124" viewBox="0 0 355 124"><polygon points="0,0 355,0 177,124" fill="#fdd22f"/></svg>
  <div class="brand-name">LUMBRA<small>Ember Oven Kitchen</small></div>
</div>

<section class="abs hero" role="img" aria-label="Close-up photo of rolled roast slices with fresh herbs"></section>
<h1 class="abs hero-title">Lets Get Lunch At<br>Lumbra !</h1>
<a class="btn btn-solid" href="#" style="top:332px;left:393px;width:120px;height:41px">TAKE OUT</a>
<a class="btn btn-line" href="#" style="top:332px;left:521px;width:158px;height:41px">RESERVATION</a>
<a class="btn btn-line" href="#" style="top:332px;left:686px;width:108px;height:41px">MENU</a>

<section class="abs info">
  <div class="divider" style="left:414px"></div>
  <div class="divider" style="left:786px"></div>
  <h2 class="heading" style="top:42px;left:62px">OPENING HOURS</h2>
  <h3 style="top:96px;left:62px">Outdoor Dining Hours</h3>
  <svg class="clock" style="top:132px" width="16" height="16" viewBox="0 0 16 16"><circle cx="8" cy="8" r="7" fill="none" stroke="#111" stroke-width="1.2"/><path d="M8 4v4l3 2" fill="none" stroke="#111" stroke-width="1.2"/></svg>
  <div class="hours" style="top:124px">Thursday &nbsp;- &nbsp;12 &nbsp;to &nbsp;8<br>Friday &nbsp;- &nbsp;12 &nbsp;to &nbsp;Late<br>Saturday &nbsp;- &nbsp;12 &nbsp;to &nbsp;Late<br>Sunday &nbsp;- &nbsp;12 &nbsp;to &nbsp;8</div>
  <h3 style="top:270px;left:62px">Takeout Hours</h3>
  <svg class="clock" style="top:306px" width="16" height="16" viewBox="0 0 16 16"><circle cx="8" cy="8" r="7" fill="none" stroke="#111" stroke-width="1.2"/><path d="M8 4v4l3 2" fill="none" stroke="#111" stroke-width="1.2"/></svg>
  <div class="hours" style="top:298px">Thursday to Sunday &nbsp;- &nbsp;12:00pm - 8:00pm</div>
  <h2 class="heading" style="top:42px;left:510px">LOCATION</h2>
  <a href="#" style="position:absolute;top:304px;left:590px;font-family:Roboto,sans-serif;font-weight:700;font-size:13px;color:#111">GO</a>
  <h2 class="heading" style="top:42px;left:804px">E-GIFT CARDS</h2>
</section>
<div class="abs map" role="img" aria-label="Street map of downtown Bexwell with the restaurant pinned"></div>
<div class="abs gift" role="img" aria-label="Gift card artwork with a red ribbon and bow">
  <p class="abs" style="top:70px;left:100px;width:218px;font-size:12px;line-height:20px;text-align:center;color:#333">Lorem Ipsum has been the industry's standard dummy text.</p>
  <p class="abs" style="top:120px;left:109px;font-family:Roboto,sans-serif;font-weight:500;font-size:19px">CODE: LMB48EOK2</p>
</div>

<h2 class="abs heading" style="top:1191px;left:0;width:1200px;text-align:center;font-size:29px">RESERVATIONS</h2>
<p class="abs" style="top:1240px;left:360px;width:480px;text-align:center;font-size:13px;line-height:21px;color:var(--muted)">Lorem Ipsum has been the industry's standard dummy text ever since the 1 an unknown printer took a galley</p>

<div class="abs res-bg" role="img" aria-label="Soft blurred photo of plated food"></div>
<div class="abs building" role="img" aria-label="Photo of the brick restaurant building on a street corner"></div>

<div class="abs order-band">
  <svg width="1200" height="380" viewBox="0 0 1200 380"><polygon points="0,7 700,70 1200,55 1200,380 0,380" fill="#fdd22f"/></svg>
</div>

<svg class="abs" style="top:1326px;left:310px" width="70" height="32" viewBox="0 0 70 32"><path d="M0 32 Q30 28 35 0 Q40 28 70 32Z" fill="#fdd22f"/></svg>
<div class="abs takeout">
  <div class="takeout-head">TAKE OUT</div>
  <p style="margin-top:26px;text-align:center;color:var(--yellow);font-weight:600;font-style:italic;font-size:14px">Thursday to Sunday 12:00pm - 8:00pm</p>
  <p style="margin:6px auto 0;width:270px;text-align:center;color:var(--paper);font-size:12px;line-height:20px">Lorem Ipsum has been the industry's standard dummy text ever since the 1500s, when an unknown printer took a galley</p>
</div>
<a class="btn btn-solid" href="#" style="top:1550px;left:267px;width:156px;height:40px;border-radius:20px">ORDER ONLINE</a>
<div class="abs box-food" role="img" aria-label="Kraft takeout box beside a burger"></div>

<h2 class="abs heading" style="top:1996px;left:114px;font-size:29px;line-height:34px">ORDER ONLINE<br>AND GET GIFT CARD</h2>
<p class="abs" style="top:2072px;left:116px;font-size:13px;color:var(--muted)">Eat Healthy</p>
<a class="btn" href="#" style="top:2102px;left:114px;width:158px;height:41px;border:2px solid var(--ink)">ORDER ONLINE</a>
<div class="abs burger" role="img" aria-label="Photo of a roast beef sandwich with onions and greens"></div>

<div class="abs portrait" role="img" aria-label="Photo of a smiling guest with a plate of tacos"></div>
<h2 class="abs heading" style="top:2300px;left:0;width:1200px;text-align:center;font-size:29px">NEWSLETTER</h2>
<p class="abs" style="top:2342px;left:0;width:1200px;text-align:center;font-size:13px;color:var(--muted)">Stay up to date with us!</p>
<div class="abs signup">
  <span class="abs" style="top:13px;left:14px;font-size:11px;color:var(--muted)">Enter Email *</span>
  <span class="abs" style="top:0;right:0;width:150px;height:42px;background:var(--yellow);display:flex;align-items:center;justify-content:center;font-family:Roboto,sans-serif;font-weight:700;font-size:14px">SUBSCRIBE</span>
</div>

<div class="tile" style="left:0;background:linear-gradient(160deg,#c9c9c4,#8e6e5d 60%,#b0443c)" role="img" aria-label="Photo of friends holding drinks in a brewery"></div>
<div class="tile" style="left:201px;background:var(--yellow);display:flex;flex-direction:column;align-items:center;justify-content:center">
  <span style="font-family:Roboto,sans-serif;font-weight:500;font-size:15px">FOLLOW US</span>
  <span style="font-size:12px;margin-top:6px">#lumbra.bexwell</span>
</div>
<div class="tile" style="left:402px;background:linear-gradient(160deg,#a7b98a,#c9a487 55%,#7d6a57)" role="img" aria-label="Photo of guests dancing on the patio"></div>
<div class="tile" style="left:603px;background:linear-gradient(160deg,#c8453a,#4f6e8f 55%,#2c2c2c)" role="img" aria-label="Photo of a guest in a red chair with a drink"></div>
<div class="tile" style="left:804px;background:linear-gradient(160deg,#a38b6f,#d8cbb9 55%,#6f5b4a)" role="img" aria-label="Photo of diners sharing plates at a table"></div>
<div class="tile" style="left:1006px;width:194px;background:linear-gradient(160deg,#5a4538,#2b2522 55%,#b95b3a)" role="img" aria-label="Photo of a cook at the kitchen counter"></div>

<footer class="abs footer">
  <h4 style="top:92px;left:175px">LOCATION</h4>
  <p style="top:123px;left:130px;width:165px">48 Alder Row<br>Bexwell, ON</p>
  <div class="abs" style="top:64px;left:422px;width:356px;text-align:center;font-family:'Archivo Black',sans-serif;font-size:31px;line-height:32px">LUMBRA<span style="display:block;font-size:12px;line-height:14px">Ember Oven Kitchen</span></div>
  <p style="top:128px;left:422px;width:356px;font-size:11px">Stay up to date with Us !</p>
  <svg class="abs" style="top:170px;left:580px" width="40" height="16" viewBox="0 0 40 16"><circle cx="8" cy="8" r="7" fill="#fdd22f"/><circle cx="30" cy="8" r="7" fill="#fdd22f"/></svg>
  <p style="top:210px;left:0;width:1200px;font-size:11px;color:#bbb"><span style="color:var(--yellow)">©LUMBRA</span> - 2021 All Rights Reserved.</p>
  <h4 style="top:92px;left:928px">CONTACT US</h4>
  <p style="top:123px;left:870px;width:215px">555-014-2287<br>hello@lumbrabexwell.example</p>
</footer>

</body>
</html>
```